Web design for new streaming audio service

We need a homepage design for a new streaming audio service. Our company is called Dunmoral, and we’re basically Vexlo for Audiobooks, Stand-Up Comedy, Lectures, Language Learning, etc. Essentially like Plumtrek for everything audio EXCEPT music.
You don’t have to code the homepage (Design Only), but it should include 3 different designs to work with 1) Web; 2) Phones; 3) Tablets.
Below is a link to a mockup of the web version which gives a good idea of what elements we want. This is just a mockup and we want you to improve it.
Once you download the mockup, please refer to the more detailed instructions below:
The following outlines the design project for the Dunmoral homepage. We have provided a rough mockup of the homepage layout that gives you a general idea of what we’re going for. There are a few elements that we are attached to, and many others where you have complete creative freedom to do whatever you think looks good.
The ZIP file includes the following:
* Mockup to see what we have in mind (dunmoral-homepage-mockup.jpg)
* Text used (dunmoral-homepage-text.txt)
* Raw image of actor (dunmoral-actor1.jpg)
* Raw images for samples (dunmoral-sample-[name].jpg)
Although we have only provided a mockup layout for the web version, we also need you to provide a mobile phone and a tablet version of the design also. It’s very possible the tablet version may be substantially similar to the web version, but the mobile phone version will likely be much different.
All of the raw files are included in the attached ZIP file. Please use our photographs and text as provided although cropping, sizing, etc. is flexible per the instructions below.
Display Requirements:
* Web Version - Minimum resolution 1024x768 (72 dpi) but should look good on 1920x1080 (72 dpi) - Page should be designed to scale to look acceptable in all resolutions in between.
* Phone Version - Minimum Zarno 4 - 640x960 (326 dpi) but should look good on Harlow Quasar T5 - 1920x1080 (441 dpi) - Page should be designed to scale to look acceptable in all resolutions and devices in between.
* Tablet Version - Minimum Bristly Ember QX 7” - 1280x800 (216 dpi) but should also look good on a Tavo Breeze - 2048x1536 (264 dpi) - Page should be designed to scale to look acceptable in all resolutions and devices in between.
Above the Fold - We want to make sure the Dunmoral logo, Member Login Link, Large Photo, Headline, Price, Button, and the first row of sample images are all “Above the fold”. As a general guideline, this means 600 pixels high on a 1024x768 72 dpi web screen. This requirement is less important on Phone versions.
Top Logo Bar - We want to retain the blue bar with the Dunmoral logo on the page, although we are open to a different size, shape and positioning if it greatly enhances the design. Please use the standard logo color, although you are welcome to use either the horizontal or vertical orientation of the logo based on your design.
Text color, font and size - Feel free to design the text in anyway you choose as long as the text is readable on the target platforms.
Buttons - Feel free to use any size, shape and colors for the buttons as long as they are obvious and clickable relative to the page. The only exception is the Chatterly button should follow the Chatterly color scheme and logo treatment (the mockup doesn’t seem 100% correct.)
Top Photograph - We want to retain the large photograph across the top of the screen although final shape and dimensions are flexible.
Size and shape of content samples (i.e. Audiobooks, Stand-Up Comedy, etc.) - Feel free to design the content samples in anyway you choose.
Three Sales Points (i.e. Listen on your Zarno…, All you can enjoy…, etc.) - The Three Sales Points are envisioned to each have a corresponding illustration which you should provide and have rights for. The placeholder is represented by a square next to the text. The color size and shape of these elements are flexible and can be designed in any way you choose.
Opt-in form - Feel free to design the opt-in form in anyway you choose as long as the text is readable and the interactivity is obvious on the target platforms.
Text links and copyright notice - Feel free to design the bottom of the page text links and copyright notice in anyway you choose.
Additional colors, graphic design elements, etc. - Feel free to use any additional colors, graphic design elements, etc. to support your design.
people who want to listen to audio through their mobile devices.
Graphic Design

```html
<!DOCTYPE html>
<html lang="en">
<head>
<meta charset="utf-8">
<title>Dunmoral</title>
<link rel="stylesheet" href="https://fonts.googleapis.com/css2?family=Open+Sans:wght@300;400;600&display=swap">
<style>
:root{
  --blue:#4fa3d8;
  --blue-soft:rgba(92,170,222,.88);
  --ink:#2e2e2e;
  --muted:#7a7a7a;
  --panel:#e6e6e6;
  --band:#ececec;
  --dark:#3a3a3a;
  --slate:#3c4a63;
  --white:#fff;
}
*{margin:0;padding:0;box-sizing:border-box}
html,body{width:1200px;height:4143px;overflow:hidden}
body{font-family:"Open Sans",Arial,sans-serif;color:var(--ink);background:var(--white);position:relative}
.abs{position:absolute}
h2.section-title{position:absolute;font-weight:300;font-size:40px;color:var(--ink);white-space:nowrap}

/* hero */
.hero{left:0;top:0;width:1200px;height:860px;background:radial-gradient(ellipse at 75% 35%,#d9a6ef 0%,#8b4fd0 30%,#3a2d8a 60%,#1a2a6a 85%),#2b2f7a}
.hero-shade{left:0;top:560px;width:1200px;height:300px;background:linear-gradient(180deg,rgba(30,30,80,0) 0%,#1b2a60 60%,#141c45 100%)}
.brand{left:34px;top:40px;width:180px;height:130px;color:var(--white);text-align:center}
.brand .mark{width:70px;height:70px;border-radius:50%;background:var(--white);margin:0 auto 8px}
.brand .name{font-size:30px;font-weight:600}
.topbar{left:235px;top:47px;width:940px;height:70px;background:var(--blue-soft);color:var(--white);font-size:15px;padding:24px 60px;white-space:nowrap}
.socialbar{left:235px;top:117px;width:940px;height:74px;background:rgba(255,255,255,.12);display:flex;align-items:center;padding-left:26px;gap:26px}
.socialbar .dot{width:20px;height:20px;border-radius:50%;background:rgba(255,255,255,.8)}
.login{position:absolute;right:0;top:0;width:170px;height:74px;background:var(--slate);color:var(--white);font-size:15px;display:flex;align-items:center;justify-content:center;gap:10px}
.nav{left:70px;top:223px;width:1105px;height:121px;background:var(--white);display:flex;align-items:center;padding-left:42px;gap:30px;font-size:21px;color:var(--blue);white-space:nowrap}
.caption{left:40px;top:422px;width:605px;height:340px;background:var(--blue-soft);color:var(--white);padding:30px 28px}
.caption h1{font-weight:400;font-size:31px;line-height:1.25;margin-bottom:16px}
.caption p{font-size:17px;line-height:1.6}
.caption .offer{display:flex;align-items:center;gap:22px;margin-top:18px}
.caption .price{font-size:26px;font-weight:600}
.caption .price small{font-size:16px;font-weight:400}
.caption .cta{background:var(--white);color:var(--blue);font-size:16px;font-weight:600;padding:10px 22px}
.arrow{width:70px;height:70px;background:var(--white);display:flex;align-items:center;justify-content:center}

/* quote */
.quote{left:0;top:910px;width:1200px;text-align:center;font-size:21px}
.avatar{left:38px;top:950px;width:70px;height:72px;background:linear-gradient(#c99a6f,#7a5a45)}
.rule{left:40px;top:1028px;width:1120px;height:2px;background:#e2e2e2}
.plus{left:570px;top:998px;width:60px;height:60px;border-radius:50%;background:#d5d5d5;color:var(--white);font-size:40px;text-align:center;line-height:58px}

/* samples */
.sample{top:1185px;width:350px;height:371px}
.pager{top:1095px;font-size:48px;color:#cfcfcf}

/* banner */
.banner{left:40px;top:1603px;width:1120px;height:197px;background:var(--panel);padding:34px 40px}
.banner h3{font-weight:400;font-size:31px;margin-bottom:8px;white-space:nowrap}
.banner p{font-size:19px;color:var(--muted);font-style:italic;width:680px;line-height:1.4}
.banner .btn{position:absolute;right:40px;top:112px;width:340px;height:54px;background:var(--blue);color:var(--white);font-size:20px;text-align:center;line-height:54px}

/* shows */
.show{left:40px;width:740px;height:220px}
.show .pic{position:absolute;left:0;top:0;width:200px;height:220px}
.show .pin{position:absolute;left:200px;top:120px;width:100px;height:100px;background:var(--dark);display:flex;align-items:center;justify-content:center}
.show .body{position:absolute;left:200px;top:0;width:540px;height:220px;background:var(--panel);padding:18px 44px 0 120px}
.show h4{font-weight:300;font-size:30px;margin-bottom:6px;white-space:nowrap}
.show .meta{font-size:16px;color:var(--muted);margin-bottom:10px}
.show .meta span{margin-right:36px}
.show p{font-size:16px;line-height:1.55;color:#555}
.show .corner{position:absolute;right:0;top:0;width:38px;height:38px;background:#bdbdbd;color:var(--white);text-align:center;line-height:36px;font-size:24px}
.tweet{left:810px;top:2100px;width:350px;height:305px;background:var(--blue);color:var(--white);font-size:22px;line-height:1.4;padding:52px 36px}
.tweet-tail{left:840px;top:2405px}
.follow{left:810px;top:2468px;font-size:17px;color:#555;display:flex;align-items:center;gap:14px}

/* voices band */
.band{left:0;top:2915px;width:1200px;height:470px;background:var(--band)}
.grid{left:40px;top:3030px;width:540px;height:352px;display:grid;grid-template-columns:repeat(6,1fr);gap:8px}
.grid div{height:82px}
.cat{left:612px;width:548px;height:62px;background:#d9d9d9;border-left:6px solid var(--blue);font-size:20px;color:var(--muted);padding:16px 26px}

/* sales points & contact */
.point{left:40px;width:540px;height:80px}
.point .icon{position:absolute;left:0;top:0;width:72px;height:72px;background:var(--blue);display:flex;align-items:center;justify-content:center}
.point .t{position:absolute;left:100px;top:6px;font-size:19px}
.point .s{position:absolute;left:100px;top:38px;font-size:17px;color:var(--muted);white-space:nowrap}
.contact-lead{left:622px;top:3590px;width:540px;font-size:17px;line-height:1.6;color:#555}
.contact-line{left:622px;font-size:17px;color:var(--muted);display:flex;align-items:center;gap:16px}
.contact-line i{width:18px;height:18px;border-radius:50%;background:#c8c8c8;display:inline-block}

.footer-rule{left:0;top:3905px;width:1200px;height:2px;background:#eee}
.foot-brand{left:40px;top:3975px;display:flex;align-items:center;gap:14px;font-size:36px;font-weight:600;color:var(--dark)}
.foot-brand .mark{width:56px;height:56px;border-radius:50%;background:var(--blue)}
.foot-links{right:40px;top:3985px;font-size:17px;color:var(--blue);display:flex;gap:22px}
.copy{right:40px;top:4020px;font-size:16px;color:var(--muted)}
</style>
</head>
<body>

<header>
  <div class="abs hero" role="img" aria-label="Listener wearing headphones under soft purple and blue light"></div>
  <div class="abs hero-shade"></div>
  <div class="abs brand"><div class="mark"></div><div class="name">Dunmoral</div></div>
  <div class="abs topbar">Audiobooks, stand-up, lectures and language lessons. Stream everything except music.</div>
  <div class="abs socialbar">
    <span class="dot"></span><span class="dot"></span><span class="dot"></span><span class="dot"></span><span class="dot"></span><span class="dot"></span><span class="dot"></span>
    <div class="login"><svg width="18" height="18"><circle cx="9" cy="5" r="4" fill="#fff"/><path d="M1 18a8 7 0 0 1 16 0z" fill="#fff"/></svg>Member Login</div>
  </div>
  <nav class="abs nav">
    <span>HOME</span><span>AUDIOBOOKS</span><span>COMEDY</span><span>LECTURES</span><span>LANGUAGES</span><span>KIDS</span><span>PLANS</span><span>HELP</span>
  </nav>
  <div class="abs caption">
    <h1>Every story, every laugh,<br>every lesson in one app</h1>
    <p>Unlimited audiobooks, stand-up specials, university lectures and language courses. Listen on your phone, tablet or computer, anytime.</p>
    <div class="offer"><span class="price">$9.99 <small>/ month</small></span><span class="cta">Start Free Trial</span></div>
  </div>
  <div class="abs arrow" style="left:650px;top:612px"><svg width="20" height="28"><path d="M4 3l12 11L4 25" fill="none" stroke="#222" stroke-width="4"/></svg></div>
  <div class="abs arrow" style="left:650px;top:692px"><svg width="20" height="28"><path d="M16 3L4 14l12 11" fill="none" stroke="#222" stroke-width="4"/></svg></div>
</header>

<section>
  <p class="abs quote">"My commute turned into a library" by Dana Ilves</p>
  <div class="abs avatar" role="img" aria-label="Member portrait"></div>
  <div class="abs rule"></div>
  <div class="abs plus">+</div>
</section>

<section>
  <h2 class="section-title" style="left:40px;top:1095px">New Audiobooks</h2>
  <div class="abs pager" style="left:1060px">&#8592;</div>
  <div class="abs pager" style="left:1110px">&#8594;</div>
  <div class="abs sample" style="left:40px;background:linear-gradient(160deg,#d88a6a,#a3443c 55%,#3d2a2a)" role="img" aria-label="Audiobook cover, memoir"></div>
  <div class="abs sample" style="left:425px;background:linear-gradient(180deg,#e8e1d4,#9a8f7f 60%,#4a4640)" role="img" aria-label="Audiobook cover, sports story"></div>
  <div class="abs sample" style="left:810px;background:linear-gradient(160deg,#6f7d86,#2d3338 60%,#111)" role="img" aria-label="Audiobook cover, noir thriller"></div>
</section>

<section class="abs banner">
  <h3>Thousands of hours of spoken audio, ready when you are</h3>
  <p>Audiobooks, comedy, lectures and language lessons, streamed or saved offline for later.</p>
  <div class="btn">START LISTENING</div>
</section>

<section>
  <h2 class="section-title" style="left:40px;top:1840px">Featured Shows</h2>
  <h2 class="section-title" style="left:810px;top:1840px">Top Picks</h2>

  <article class="abs show" style="top:1935px">
    <div class="pic" style="background:linear-gradient(135deg,#2d5fae,#7fb0d8)" role="img" aria-label="Audiobook cover art"></div>
    <div class="body"><h4>The Quiet Harbor ...</h4><div class="meta"><span>Audiobook</span><span>Listen Now</span></div><p>A gripping family saga read by its author, twelve hours of storytelling for long drives.</p><div class="corner">&#8211;</div></div>
    <div class="pin"><svg width="30" height="30"><path d="M8 4l18 11L8 26z" fill="#fff"/></svg></div>
  </article>
  <article class="abs show" style="top:2170px">
    <div class="pic" style="background:linear-gradient(135deg,#6a3c8e,#c46fb2)" role="img" aria-label="Comedy special artwork"></div>
    <div class="body"><h4>Late Night Laughs ...</h4><div class="meta"><span>Stand-Up Comedy</span><span>Listen Now</span></div><p>A full hour recorded live, packed with sharp stories about family, travel and work.</p><div class="corner">&#8211;</div></div>
    <div class="pin"><svg width="30" height="30"><path d="M8 4l18 11L8 26z" fill="#fff"/></svg></div>
  </article>
  <article class="abs show" style="top:2405px">
    <div class="pic" style="background:linear-gradient(135deg,#1d1d3a,#3c6eb4)" role="img" aria-label="Lecture series artwork"></div>
    <div class="body"><h4>Stars and Atoms ...</h4><div class="meta"><span>Lecture Series</span><span>Listen Now</span></div><p>Twenty short talks that explain the universe, from tiny particles to distant galaxies.</p><div class="corner">+</div></div>
    <div class="pin"><svg width="30" height="30"><path d="M8 4l18 11L8 26z" fill="#fff"/></svg></div>
  </article>
  <article class="abs show" style="top:2640px">
    <div class="pic" style="background:linear-gradient(135deg,#e9c9a0,#7aa36a)" role="img" aria-label="Language course artwork"></div>
    <div class="body"><h4>Spanish in 30 Days ...</h4><div class="meta"><span>Language Learning</span><span>Listen Now</span></div><p>Short daily lessons with native speakers that build real everyday conversation skills.</p><div class="corner">&#8211;</div></div>
    <div class="pin"><svg width="30" height="30"><path d="M8 4l18 11L8 26z" fill="#fff"/></svg></div>
  </article>

  <h2 class="section-title" style="left:810px;top:1985px;color:var(--blue)">Chirpline</h2>
  <div class="abs tweet">Just finished a whole audiobook on my commute this week. New comedy drops Friday!</div>
  <svg class="abs tweet-tail" width="40" height="30"><path d="M0 0h40L10 30z" fill="#4fa3d8"/></svg>
  <div class="abs follow"><svg width="26" height="26"><circle cx="13" cy="13" r="12" fill="#4fa3d8"/></svg>Follow us on Chirpline</div>
</section>

<section>
  <div class="abs band"></div>
  <h2 class="section-title" style="left:40px;top:2945px">Voices</h2>
  <h2 class="section-title" style="left:612px;top:2945px">Categories</h2>
  <div class="abs grid">
    <div style="background:#7b4a3a" role="img" aria-label="Narrator photo"></div><div style="background:#c79a6c" role="img" aria-label="Narrator photo"></div><div style="background:#3a2f2c" role="img" aria-label="Narrator photo"></div><div style="background:#8a5b6e" role="img" aria-label="Narrator photo"></div><div style="background:#b47b5e" role="img" aria-label="Narrator photo"></div><div style="background:#4b3f52" role="img" aria-label="Narrator photo"></div>
    <div style="background:#a56b57" role="img" aria-label="Narrator photo"></div><div style="background:#2f2a2a" role="img" aria-label="Narrator photo"></div><div style="background:#d3a47f" role="img" aria-label="Narrator photo"></div><div style="background:#6b4b3c" role="img" aria-label="Narrator photo"></div><div style="background:#9d8a7a" role="img" aria-label="Narrator photo"></div><div style="background:#3d3636" role="img" aria-label="Narrator photo"></div>
    <div style="background:#c08f70" role="img" aria-label="Narrator photo"></div><div style="background:#5a4742" role="img" aria-label="Narrator photo"></div><div style="background:#8c6f5e" role="img" aria-label="Narrator photo"></div><div style="background:#e0c0a4" role="img" aria-label="Narrator photo"></div><div style="background:#463a3e" role="img" aria-label="Narrator photo"></div><div style="background:#a98069" role="img" aria-label="Narrator photo"></div>
    <div style="background:#3b3231" role="img" aria-label="Narrator photo"></div><div style="background:#b58d77" role="img" aria-label="Narrator photo"></div><div style="background:#7a5c50" role="img" aria-label="Narrator photo"></div><div style="background:#c9a38a" role="img" aria-label="Narrator photo"></div><div style="background:#574a4b" role="img" aria-label="Narrator photo"></div><div style="background:#9b735e" role="img" aria-label="Narrator photo"></div>
  </div>
  <div class="abs cat" style="top:3040px">Audiobooks</div>
  <div class="abs cat" style="top:3110px">Stand-Up Comedy</div>
  <div class="abs cat" style="top:3180px">Lectures</div>
  <div class="abs cat" style="top:3250px">Language Learning</div>
  <div class="abs cat" style="top:3320px">Kids and Family</div>
</section>

<section>
  <h2 class="section-title" style="left:40px;top:3490px">Why Dunmoral</h2>
  <h2 class="section-title" style="left:622px;top:3490px">Contact Us</h2>
  <div class="abs point" style="top:3597px"><div class="icon"><svg width="26" height="40"><rect x="2" y="2" width="22" height="36" rx="4" fill="none" stroke="#fff" stroke-width="3"/><circle cx="13" cy="32" r="2" fill="#fff"/></svg></div><div class="t">Listen on your Zarno</div><div class="s">Stream on phones, tablets and the web</div></div>
  <div class="abs point" style="top:3685px"><div class="icon"><svg width="36" height="36"><path d="M18 4v28M4 18h28" stroke="#fff" stroke-width="4"/></svg></div><div class="t">All you can enjoy</div><div class="s">Unlimited listening for one monthly price</div></div>
  <div class="abs point" style="top:3773px"><div class="icon"><svg width="36" height="30"><path d="M3 15l10 10L33 4" fill="none" stroke="#fff" stroke-width="4"/></svg></div><div class="t">Try it free</div><div class="s">Cancel anytime, no strings attached</div></div>

  <p class="abs contact-lead">Questions about your membership? Write to us, we are happy to help.</p>
  <div class="abs contact-line" style="top:3672px"><i></i>Dunmoral, 18 Larkfield Row, Suite 4</div>
  <div class="abs contact-line" style="top:3712px"><i></i>T: (010) 52 71 38 20</div>
  <div class="abs contact-line" style="top:3752px"><i></i>M: +0042 310 775 214</div>
  <div class="abs contact-line" style="top:3792px"><i></i>hello@dunmoral.net</div>
  <div class="abs contact-line" style="top:3832px"><i></i>www.dunmoral.net</div>
</section>

<footer>
  <div class="abs footer-rule"></div>
  <div class="abs foot-brand"><span class="mark"></span>Dunmoral</div>
  <nav class="abs foot-links"><span>Home</span><span>Audiobooks</span><span>Comedy</span><span>Lectures</span><span>Plans</span><span>Contact Us</span></nav>
  <p class="abs copy">&copy; 2014 Dunmoral. All Rights Reserved.</p>
</footer>

</body>
</html>
```